Blind Rivet Product catalogue

Need a design in wordpress with a productcatalogue where i present all products. This is a B2B business. The products is Blindrivets and Blindrivet nuts and accessories to this. I only want the basic information and also technical specification.

This is a subcompany to my existing company k7.m3.se but specializing in a subcategory

Businesses using blind rivet technology.

Industrial

Sans Serif

Must have
• Three different categories for the products; Blind Rivets - Blind Rivet Nut - Riveting Tools
Nice to have
• Possible to ad login for more information of the different sizes

```html
<!DOCTYPE html>
<html lang="en">
<head>
<meta charset="utf-8">
<title>Nitora – Blind Rivet Catalogue</title>
<link href="https://fonts.googleapis.com/css2?family=Montserrat:wght@400;600;700;800&family=Open+Sans:wght@400;600&display=swap" rel="stylesheet">
<style>
:root{
  --red:#e3202a;
  --green:#3a9a3c;
  --price:#6cb33f;
  --dark:#141414;
  --hero:#1d1d1f;
  --ink:#222;
  --muted:#666;
  --light:#f2f2f2;
  --line:#dcdcdc;
  --white:#fff;
}
*{margin:0;padding:0;box-sizing:border-box}
html,body{width:1200px;height:2736px;overflow:hidden;background:var(--white)}
body{font-family:"Open Sans",Arial,sans-serif;color:var(--ink);position:relative}
h1,h2,h3,.nav,.btn,.brand{font-family:"Montserrat",Arial,sans-serif}

/* hero */
.hero{position:absolute;top:0;left:0;width:1200px;height:620px;background:linear-gradient(100deg,#2a2724 0%,#1a1a1c 55%,#111 100%);overflow:hidden}
.hero-photo{position:absolute;inset:0;background:radial-gradient(ellipse at 30% 40%,rgba(120,95,70,.35),transparent 60%)}
.hero-cut{position:absolute;right:0;bottom:0}
.hero-product{position:absolute;left:820px;top:250px;width:240px;height:260px;border-radius:40px;background:linear-gradient(135deg,#f4f4f4,#9ea3a8 60%,#6c7075);transform:rotate(-35deg)}
.topbar{position:absolute;top:0;left:0;width:1200px;height:84px;display:flex;align-items:center;padding:0 40px 0 120px;background:rgba(0,0,0,.25)}
.brand{display:flex;align-items:center;gap:10px;color:var(--white);font-weight:800;font-size:22px;letter-spacing:1px}
.brand-mark{width:18px;height:18px;background:var(--red)}
.nav{display:flex;gap:30px;margin-left:auto;list-style:none;color:var(--white);font-size:13px;font-weight:600}
.nav-btns{display:flex;gap:10px;margin-left:26px}
.btn{display:inline-block;font-size:13px;font-weight:700;text-transform:uppercase;color:var(--white);padding:9px 18px;border-radius:3px}
.btn-green{background:var(--green);text-transform:none}
.btn-red{background:var(--red)}
.hero-text{position:absolute;left:172px;top:118px;color:var(--white)}
.hero-text h1{font-size:84px;font-weight:700;line-height:1.1}
.hero-text p{width:380px;margin-top:22px;font-size:15px;line-height:1.45;font-weight:600}
.hero-text .btn{margin-top:38px;padding:13px 26px;border-radius:24px}
.arrows{position:absolute;left:172px;top:505px;display:flex;gap:20px}

/* sections */
.title{font-size:32px;font-weight:700;text-align:center;letter-spacing:1px}
.title::after{content:"";display:block;width:56px;height:3px;background:var(--red);margin:14px auto 0}

.about{position:absolute;top:620px;left:0;width:1200px;height:580px}
.about-frame{position:absolute;left:150px;top:800px;width:300px;height:360px;background:var(--red)}
.about-photo{position:absolute;left:172px;top:700px;width:388px;height:440px;background:linear-gradient(135deg,#5a4a3a,#2b2520 60%,#8a6a40)}
.about-text{position:absolute;left:600px;top:716px;width:430px}
.about-text h2{font-size:32px;font-weight:700;letter-spacing:1px}
.about-text h2::after{content:"";display:block;width:56px;height:3px;background:var(--red);margin-top:14px}
.about-text p{font-size:14px;line-height:1.6;color:var(--muted);margin-top:22px}

.products{position:absolute;top:1200px;left:0;width:1200px;height:600px;background:var(--light);padding-top:60px}
.cards{display:flex;gap:28px;justify-content:center;margin-top:46px}
.card{width:268px;height:420px;background:var(--white);text-align:center;padding-top:24px}
.card-img{width:200px;height:180px;margin:0 auto;background:linear-gradient(135deg,#eee,#a9adb2);border-radius:8px}
.price{font-family:"Montserrat",Arial,sans-serif;color:var(--price);font-weight:700;font-size:22px;margin-top:30px}
.card h3{font-size:15px;font-weight:600;text-transform:uppercase;margin-top:10px;color:#444}
.btn-outline{margin-top:20px;color:#444;border:1px solid #999;font-size:11px;padding:8px 18px}

.blog{position:absolute;top:1800px;left:0;width:1200px;height:600px;padding-top:60px}
.post-main{position:absolute;left:172px;top:148px;width:416px}
.post-img{background:linear-gradient(135deg,#4a3c2e,#222 60%,#7a5c38)}
.post-main .post-img{height:284px}
.post h3{font-size:17px;font-weight:700;text-transform:uppercase;line-height:1.3;margin-top:18px}
.post p{font-size:12px;line-height:1.5;color:var(--muted);margin-top:8px}
.date{display:block;font-size:11px;font-weight:700;color:var(--red);margin-top:10px}
.post-side{position:absolute;left:608px;width:420px;display:flex;gap:12px}
.post-side .post-img{width:208px;height:180px;flex:none}
.post-side h3{margin-top:10px}
.s1{top:148px}.s2{top:348px}
.s2 .post-img{background:linear-gradient(135deg,#6d9ac4,#2c4f7a 60%,#b6c6d6)}

.footer{position:absolute;top:2400px;left:0;width:1200px;height:336px;background:var(--dark);color:#bbb}
.footer .brand{position:absolute;left:220px;top:64px}
.socials{position:absolute;left:226px;top:116px;display:flex;gap:12px}
.socials span{width:26px;height:26px;border-radius:50%;background:var(--red)}
.col{position:absolute;top:50px;width:180px}
.col h4{font-family:"Montserrat",Arial,sans-serif;color:var(--white);font-size:15px;font-weight:700;margin-bottom:16px}
.col li{list-style:none;font-size:11px;line-height:2;color:#999}
.c1{left:424px}.c2{left:660px}.c3{left:888px}
.copy{position:absolute;left:172px;top:298px;font-size:11px;color:#888}
.phone{position:absolute;left:860px;top:288px;font-family:"Montserrat",Arial,sans-serif;font-weight:700;font-size:17px;color:var(--red);display:flex;align-items:center;gap:8px}
</style>
</head>
<body>

<header class="hero">
  <div class="hero-photo" role="img" aria-label="Workshop background with riveting work"></div>
  <svg class="hero-cut" width="620" height="400" viewBox="0 0 620 400"><polygon points="0,400 620,0 620,400" fill="#fff"/></svg>
  <div class="hero-product" role="img" aria-label="Steel blind rivet nut product shot"></div>
  <div class="topbar">
    <div class="brand"><span class="brand-mark"></span>NITORA</div>
    <ul class="nav"><li>Home</li><li>Items</li><li>Tools</li><li>Info</li><li>Docs</li><li>News</li><li>Other info</li></ul>
    <div class="nav-btns"><span class="btn btn-green">Contact Us</span><span class="btn btn-red">Log In</span></div>
  </div>
  <div class="hero-text">
    <h1>Blind Rivet</h1>
    <p>Sed ut perspiciatis unde omnis iste natus error sit voluptatem accusantium doloremque laudantium, totam rem.</p>
    <span class="btn btn-red">Learn More</span>
  </div>
  <div class="arrows">
    <svg width="20" height="30" viewBox="0 0 20 30"><path d="M16 3L4 15l12 12" stroke="#fff" stroke-width="3" fill="none"/></svg>
    <svg width="20" height="30" viewBox="0 0 20 30"><path d="M4 3l12 12L4 27" stroke="#fff" stroke-width="3" fill="none"/></svg>
  </div>
</header>

<section class="about-block">
  <div class="about-frame"></div>
  <div class="about-photo" role="img" aria-label="Worker using a riveting tool"></div>
  <div class="about-text">
    <h2>ABOUT US</h2>
    <p>Nitora AB is a wholesale company that caters to other companies. Our range consists of stainless steel products for mounting and riveting applications. We have the widest and deepest range of stainless steel on the market. Our attachments comply with DIN standards and ISO standards. Please contact us and we will give prices for products that apply to your business.</p>
    <p>Please note that we only sell wholesale packaging. The minimum order quantity per pack can be found at the bottom left of each product. We also reserve the right to change the packaging size to the one our supplier sends.</p>
  </div>
</section>

<section class="products">
  <h2 class="title">OUR PRODUCTS</h2>
  <div class="cards">
    <div class="card"><div class="card-img" role="img" aria-label="Blind rivets"></div><div class="price">24,20 KR</div><h3>Blind Rivets</h3><span class="btn btn-outline">Buy Now</span></div>
    <div class="card"><div class="card-img" role="img" aria-label="Blind rivet nut"></div><div class="price">24,20 KR</div><h3>Blind Rivet Nut</h3><span class="btn btn-outline">Buy Now</span></div>
    <div class="card"><div class="card-img" role="img" aria-label="Cordless riveting tool"></div><div class="price">24,20 KR</div><h3>Riveting Tools</h3><span class="btn btn-outline">Buy Now</span></div>
  </div>
</section>

<section class="blog">
  <h2 class="title">LATEST BLOG</h2>
  <article class="post post-main">
    <div class="post-img" role="img" aria-label="Hands working with a riveting tool"></div>
    <h3>Lorem ipsum dolor sit amet</h3>
    <p>Sed ut perspiciatis unde omnis iste natus error sit voluptatem accusantium doloremque laudantium, totam rem aperiam.</p>
    <span class="date">APR 08 2020</span>
  </article>
  <article class="post post-side s1">
    <div class="post-img" role="img" aria-label="Metal workshop"></div>
    <div><h3>Lorem ipsum dolor or sit tincid</h3><p>Sed ut perspiciatis unde omnis iste natus error sit voluptatem accusantium doloremque laudantium totam rem aperiam eaque ipsa.</p><span class="date">APR 08 2020</span></div>
  </article>
  <article class="post post-side s2">
    <div class="post-img" role="img" aria-label="Technician assembling parts"></div>
    <div><h3>Lorem ipsum dolor or sit tincid</h3><p>Sed ut perspiciatis unde omnis iste natus error sit voluptatem accusantium doloremque laudantium totam rem aperiam eaque ipsa.</p><span class="date">APR 08 2020</span></div>
  </article>
</section>

<footer class="footer">
  <div class="brand"><span class="brand-mark"></span>NITORA</div>
  <div class="socials"><span></span><span></span><span></span></div>
  <div class="col c1"><h4>Products</h4><ul><li>Blind rivets steel</li><li>Blind rivets aluminium</li><li>Blind rivet nuts</li><li>Riveting tools</li><li>Accessories</li><li>Technical specifications</li></ul></div>
  <div class="col c2"><h4>Account</h4><ul><li>Log in</li><li>Register account</li><li>Order history</li><li>Price lists</li><li>Saved products</li><li>Delivery terms</li></ul></div>
  <div class="col c3"><h4>Other Links</h4><ul><li>About us</li><li>Contact us</li><li>Latest blog</li><li>Terms of sale</li><li>Privacy policy</li><li>Parent company k7.m3.se</li></ul></div>
  <div class="copy">Copyright 2020 All Rights Reserved</div>
  <div class="phone"><svg width="18" height="18" viewBox="0 0 24 24"><path fill="#e3202a" d="M6.6 10.8a15 15 0 006.6 6.6l2.2-2.2a1 1 0 011-.25 11 11 0 003.5.55 1 1 0 011 1V20a1 1 0 01-1 1A17 17 0 013 4a1 1 0 011-1h3.5a1 1 0 011 1c0 1.25.2 2.4.55 3.5a1 1 0 01-.25 1z"/></svg>Telefon: 0300-41 52 63</div>
</footer>

</body>
</html>
```